1876 Basins & Spouts Business Card

I'm wanting to get a business card designed. Our business is 1876 Basins & Spouts
Details for the card:

1876 Basins & Spouts
Name: Harold Vesk
Email: harold@1876basinsandspouts.com.au
Website: www.1876basinsandspouts.com.au
Mobile: 0438 260 947
Phone: 02 7481 3926

Font of Basins & Spouts is called Snell Roundhand. Not sue what font logo text is.

I'm thinking two sided but it doesn't have to be.

```html
<!DOCTYPE html>
<html lang="en">
<head>
<meta charset="utf-8">
<title>1876 Basins &amp; Spouts Business Card</title>
<link rel="stylesheet" href="https://fonts.googleapis.com/css2?family=Open+Sans:wght@400;600&family=Pinyon+Script&display=swap">
<style>
  :root {
    --page: #2b2b2b;
    --card: #1c1c1c;
    --ink: #f2f2f2;
    --ink-soft: #bdbdbd;
    --rule: #3d3d3d;
  }
  * { margin: 0; padding: 0; box-sizing: border-box; }
  html, body { width: 1200px; height: 900px; overflow: hidden; }
  body {
    background: var(--page);
    font-family: "Open Sans", Arial, sans-serif;
    color: var(--ink);
    position: relative;
  }
  .card {
    position: absolute;
    left: 330px;
    width: 540px;
    height: 310px;
    background: var(--card);
    border-radius: 22px;
    overflow: hidden;
    box-shadow: 0 18px 40px rgba(0,0,0,.55);
  }
  .card--back { top: 105px; }
  .card--front { top: 485px; }

  .brand-name {
    position: absolute;
    font-weight: 600;
    color: var(--ink);
    white-space: nowrap;
  }
  .card--back .brand-name {
    left: 0; right: 0; top: 110px;
    text-align: center;
    font-size: 28px;
    letter-spacing: .5px;
  }
  .brand-dot {
    display: inline-block;
    width: 10px; height: 10px;
    border-radius: 50%;
    background: var(--ink);
    vertical-align: middle;
    margin-right: 12px;
    position: relative; top: -3px;
  }
  .back-url {
    position: absolute;
    right: 58px; bottom: 58px;
    font-size: 13px;
    font-weight: 600;
    color: var(--ink);
  }

  .card--front .brand-name {
    left: 150px; top: 50px;
    font-size: 24px;
  }
  .tagline {
    position: absolute;
    left: 150px; top: 86px;
    font-size: 9px;
    color: var(--ink-soft);
    letter-spacing: .3px;
    white-space: nowrap;
  }
  .rule {
    position: absolute;
    height: 1px;
    background: var(--rule);
  }
  .rule--top { left: 150px; right: 40px; top: 108px; }
  .rule--name { left: 200px; right: 40px; top: 190px; }

  .online {
    position: absolute;
    right: 40px; top: 132px;
    list-style: none;
    font-size: 15px;
    line-height: 21px;
    color: var(--ink-soft);
    text-align: right;
  }
  .person-name {
    position: absolute;
    left: 36px; top: 192px;
    font-family: "Pinyon Script", cursive;
    font-size: 30px;
    line-height: 40px;
    color: var(--ink);
    white-space: nowrap;
  }
  .phones {
    position: absolute;
    left: 40px; top: 240px;
    list-style: none;
    font-size: 17px;
    line-height: 23px;
    color: var(--ink-soft);
  }
  .contact-item { display: flex; align-items: center; gap: 8px; white-space: nowrap; }
  .online .contact-item { justify-content: flex-end; }
  .icon { width: 14px; height: 14px; fill: var(--ink); flex: none; }
</style>
</head>
<body>

<section class="card card--back" aria-label="Card back">
  <div class="brand-name"><span class="brand-dot"></span>1876 Basins &amp; Spouts</div>
  <div class="back-url">www.1876basinsandspouts.com.au</div>
</section>

<section class="card card--front" aria-label="Card front">
  <div class="brand-name">1876 Basins &amp; Spouts</div>
  <div class="tagline">Classic forms shaped for calm everyday living</div>
  <div class="rule rule--top"></div>

  <ul class="online">
    <li class="contact-item">harold@1876basinsandspouts.com.au
      <svg class="icon" viewBox="0 0 14 14" aria-hidden="true"><rect x="1" y="3" width="12" height="8" rx="1"/><path d="M1.5 3.5 7 8l5.5-4.5" stroke="#1c1c1c" stroke-width="1.2" fill="none"/></svg>
    </li>
    <li class="contact-item">www.1876basinsandspouts.com.au
      <svg class="icon" viewBox="0 0 14 14" aria-hidden="true"><circle cx="7" cy="7" r="6"/><path d="M1 7h12M7 1c-2.5 3-2.5 9 0 12M7 1c2.5 3 2.5 9 0 12" stroke="#1c1c1c" stroke-width="1" fill="none"/></svg>
    </li>
  </ul>

  <div class="rule rule--name"></div>
  <div class="person-name">Harold Vesk</div>

  <ul class="phones">
    <li class="contact-item">
      <svg class="icon" viewBox="0 0 14 14" aria-hidden="true"><path d="M1 5c0-2 2-3 6-3s6 1 6 3l-2 1-1-2H4L3 6zM3 7h8l1 5H2z"/></svg>
      0438 260 947
    </li>
    <li class="contact-item">
      <svg class="icon" viewBox="0 0 14 14" aria-hidden="true"><rect x="3" y="1" width="8" height="12" rx="1.5"/><rect x="4.5" y="3" width="5" height="7" fill="#1c1c1c"/></svg>
      02 7481 3926
    </li>
  </ul>
</section>

</body>
</html>
```